Executive Business Card for Healthcare Company [Need Today]

I need a business card design for a healthcare company. The only branding the company has thus far is a logo. The cards will be utilized by company executives. The design I envision will be vibrant and appealing but with a corporate feel. They shouldn't be too casual or playful. I would like to complete this project TODAY if possible.

Target Market(s)

Healthcare vendors, other executives in healthcare and pharmaceuticals

Industry/Entity Type

Pharmaceutical

Contact Information for Business Card

See attachment

Font styles to use
Serif
Sans Serif

Colors

Designer to choose colors to be used in the design.

```html
<!DOCTYPE html>
<html lang="en">
<head>
<meta charset="utf-8">
<title>Marlow Therapeutics – Business Card</title>
<link href="https://fonts.googleapis.com/css2?family=Didact+Gothic&display=swap" rel="stylesheet">
<style>
  :root {
    --bg: #262626;
    --teal: #36bfc6;
    --teal-faint: rgba(255, 255, 255, 0.16);
    --green: #6cc49a;
    --white: #ffffff;
    --grey: #6b6b6b;
    --card-w: 900px;
    --card-h: 514px;
  }
  * { box-sizing: border-box; margin: 0; padding: 0; }
  html, body {
    width: 1200px; height: 1189px; overflow: hidden;
    background: var(--bg);
    font-family: "Didact Gothic", "Century Gothic", sans-serif;
  }
  .canvas {
    position: relative; width: 1200px; height: 1189px;
  }
  .card {
    position: absolute; left: 150px;
    width: var(--card-w); height: var(--card-h);
    border-radius: 30px; overflow: hidden;
    box-shadow: 0 18px 40px rgba(0,0,0,0.55);
  }
  /* Front */
  .card-front { top: 54px; background: var(--teal); }
  .front-ring {
    position: absolute; left: -120px; top: 40px;
    width: 480px; height: 480px; border-radius: 50%;
    border: 18px solid var(--teal-faint);
  }
  .front-lockup {
    position: absolute; left: 0; right: 0; top: 0; bottom: 0;
    display: flex; align-items: center; justify-content: center; gap: 22px;
  }
  .lockup-dot {
    width: 110px; height: 110px; border-radius: 50%;
    border: 4px solid var(--white);
  }
  .lockup-rule { width: 2px; height: 90px; background: var(--white); }
  .lockup-name {
    color: var(--white); font-size: 40px; letter-spacing: 0.5px; line-height: 1;
  }
  /* Back */
  .card-back { top: 622px; background: var(--white); }
  .edge-dot {
    position: absolute; left: -22px; top: 92px;
    width: 44px; height: 44px; border-radius: 50%; background: var(--teal);
  }
  .person { position: absolute; left: 62px; top: 78px; }
  .person-name { color: var(--teal); font-size: 31px; font-weight: 700; letter-spacing: 0.3px; }
  .person-title { color: var(--grey); font-size: 21px; margin-top: 2px; }
  .contacts { position: absolute; left: 100px; top: 250px; list-style: none; }
  .contacts li {
    display: flex; align-items: center; gap: 12px;
    color: var(--grey); font-size: 23px; line-height: 34px;
  }
  .contact-icon { width: 22px; height: 22px; flex: none; }
  .company { position: absolute; left: 128px; top: 378px; }
  .company-name { color: var(--teal); font-size: 25px; }
  .company-address { color: var(--grey); font-size: 25px; line-height: 33px; }
  .brand-ring {
    position: absolute; right: 74px; top: 72px;
    width: 370px; height: 370px; border-radius: 50%;
    border: 11px solid var(--green);
    display: flex; align-items: center; justify-content: center;
  }
  .brand-name {
    color: var(--teal); font-size: 38px; text-align: center; line-height: 1.15;
  }
</style>
</head>
<body>
<main class="canvas">

  <section class="card card-front" aria-label="Card front">
    <div class="front-ring" aria-hidden="true"></div>
    <div class="front-lockup">
      <div class="lockup-dot" aria-hidden="true"></div>
      <div class="lockup-rule" aria-hidden="true"></div>
      <div class="lockup-name">Marlow Therapeutics</div>
    </div>
  </section>

  <section class="card card-back" aria-label="Card back">
    <div class="edge-dot" aria-hidden="true"></div>
    <div class="person">
      <div class="person-name">Daniel Reyes</div>
      <div class="person-title">Senior Director of Marketing</div>
    </div>

    <ul class="contacts">
      <li>
        <svg class="contact-icon" viewBox="0 0 22 22" aria-hidden="true">
          <circle cx="11" cy="11" r="10" fill="none" stroke="#6cc49a" stroke-width="2"/>
          <rect x="7" y="5.5" width="8" height="11" rx="1.2" fill="none" stroke="#6cc49a" stroke-width="1.6"/>
        </svg>
        555-214-7730
      </li>
      <li>
        <svg class="contact-icon" viewBox="0 0 22 22" aria-hidden="true">
          <circle cx="11" cy="11" r="10" fill="none" stroke="#6cc49a" stroke-width="2"/>
          <path d="M6 9.5c0-2 2-3 5-3s5 1 5 3l-2 .5-.5-1.5h-5L8 10z M7.5 11h7l1 4h-9z" fill="#6cc49a"/>
        </svg>
        555-318-4062
      </li>
      <li>
        <svg class="contact-icon" viewBox="0 0 22 22" aria-hidden="true">
          <circle cx="11" cy="11" r="10" fill="#6cc49a"/>
          <rect x="5.5" y="7" width="11" height="8" fill="none" stroke="#fff" stroke-width="1.4"/>
          <path d="M5.5 7l5.5 4.5L16.5 7" fill="none" stroke="#fff" stroke-width="1.4"/>
        </svg>
        dreyes@marlowrx.com
      </li>
    </ul>

    <div class="company">
      <div class="company-name">Marlow Therapeutics, LLC</div>
      <div class="company-address">118 W Clayton Street<br>Ashford, GA 30612</div>
    </div>

    <div class="brand-ring">
      <div class="brand-name">Marlow<br>Therapeutics</div>
    </div>
  </section>

</main>
</body>
</html>
```